Modern Business Card

Modern professional business card with more than just logo and demographic info. Something memorable.

We are a trendy/modern chiropractic group with an emphasis on neurology, hence the minimalist-type brain logo. We want to convey that modern and technical aspect with professionalism and the elite nature of our practice environment.

```html
<!DOCTYPE html>
<html lang="en">
<head>
<meta charset="utf-8">
<title>Meridian Chiropractic – Business Card</title>
<link href="https://fonts.googleapis.com/css2?family=Montserrat:wght@400;600;700&display=swap" rel="stylesheet">
<style>
  :root {
    --brand-blue: #4a84c6;
    --brand-blue-light: #5b93d2;
    --ink: #1f1f1f;
    --text-grey: #555a60;
    --swoosh-grey: #6b6e72;
    --card-white: #ffffff;
    --stage: #e9ebee;
  }
  * { margin: 0; padding: 0; box-sizing: border-box; }
  html, body {
    width: 1200px; height: 909px; overflow: hidden;
    background: var(--stage);
    font-family: "Montserrat", sans-serif;
  }
  .canvas { position: relative; width: 1200px; height: 909px; }

  .card {
    position: absolute;
    width: 600px; height: 343px;
    border-radius: 3px;
    overflow: hidden;
    box-shadow: 0 6px 18px rgba(0,0,0,.18);
  }

  /* Back side */
  .card--back {
    left: 60px; top: 80px;
    background: linear-gradient(160deg, var(--brand-blue-light) 0%, var(--brand-blue) 60%, #4580c3 100%);
    display: flex; align-items: center; justify-content: center;
  }
  .wordmark {
    display: flex; align-items: center; gap: 14px;
    font-weight: 600; letter-spacing: .12em; text-transform: uppercase;
    line-height: 1.1;
  }
  .wordmark__dot { border-radius: 50%; flex: none; }
  .card--back .wordmark { color: var(--card-white); font-size: 30px; }
  .card--back .wordmark__dot { width: 34px; height: 34px; background: var(--card-white); }
  .wordmark__sub { display: block; font-size: .62em; letter-spacing: .16em; }

  /* Front side */
  .card--front { left: 540px; top: 486px; background: var(--card-white); }
  .card__swoosh { position: absolute; inset: 0; width: 100%; height: 100%; }
  .card--front .wordmark {
    position: absolute; right: 40px; top: 40px;
    color: var(--ink); font-size: 22px; text-align: left;
  }
  .card--front .wordmark__dot { width: 26px; height: 26px; background: var(--brand-blue); }

  .contact { position: absolute; left: 0; top: 118px; }
  .contact__identity { position: relative; padding-left: 46px; }
  .contact__identity::before {
    content: ""; position: absolute; left: 18px; top: 4px;
    width: 14px; height: 38px; background: var(--brand-blue);
  }
  .contact__name {
    color: var(--brand-blue); font-weight: 700; font-size: 19px; letter-spacing: .02em;
  }
  .contact__role { color: var(--text-grey); font-size: 12px; margin-top: 2px; }
  .contact__address {
    color: var(--text-grey); font-size: 12px; line-height: 1.45;
    margin: 22px 0 0 46px;
  }
  .contact__list { list-style: none; margin: 20px 0 0 46px; }
  .contact__item {
    display: flex; align-items: center; gap: 8px;
    color: var(--text-grey); font-size: 12px; line-height: 1.7;
  }
  .contact__icon {
    width: 13px; height: 13px; background: var(--brand-blue);
    border-radius: 2px; flex: none;
  }
</style>
</head>
<body>
<main class="canvas">

  <section class="card card--back" aria-label="Business card back">
    <div class="wordmark">
      <span class="wordmark__dot"></span>
      <span>Meridian<span class="wordmark__sub">Chiropractic</span></span>
    </div>
  </section>

  <section class="card card--front" aria-label="Business card front">
    <svg class="card__swoosh" viewBox="0 0 600 343" preserveAspectRatio="none" aria-hidden="true">
      <path d="M120 343 C 300 330, 380 205, 600 200 L600 343 Z" fill="var(--brand-blue)"/>
      <path d="M70 343 C 210 335, 330 300, 430 232 C 330 310, 220 338, 110 343 Z" fill="var(--ink)"/>
      <path d="M40 343 C 200 338, 320 318, 420 250 C 320 325, 200 342, 80 343 Z" fill="var(--swoosh-grey)"/>
    </svg>

    <div class="wordmark">
      <span class="wordmark__dot"></span>
      <span>Meridian<span class="wordmark__sub">Chiropractic</span></span>
    </div>

    <div class="contact">
      <div class="contact__identity">
        <p class="contact__name">DANIEL CROWE</p>
        <p class="contact__role">Senior Partner</p>
      </div>
      <p class="contact__address">12 Ashford Lane Greenhill,<br>Riverton, 4021</p>
      <ul class="contact__list">
        <li class="contact__item">
          <svg class="contact__icon" viewBox="0 0 13 13" aria-hidden="true"><rect width="13" height="13" rx="2" fill="var(--brand-blue)"/><path d="M4 3.2l1.3 1.6-.7.8c.5 1 1.3 1.8 2.3 2.3l.8-.7 1.6 1.3-.8 1.2C6 9.4 3.6 7 3 4z" fill="#fff"/></svg>
          +100 555 0142
        </li>
        <li class="contact__item">
          <svg class="contact__icon" viewBox="0 0 13 13" aria-hidden="true"><rect width="13" height="13" rx="2" fill="var(--brand-blue)"/><rect x="4.3" y="2.5" width="4.4" height="8" rx=".8" fill="none" stroke="#fff" stroke-width="1"/></svg>
          +100 555 0187
        </li>
        <li class="contact__item">
          <svg class="contact__icon" viewBox="0 0 13 13" aria-hidden="true"><rect width="13" height="13" rx="2" fill="var(--brand-blue)"/><rect x="2.8" y="4" width="7.4" height="5" fill="none" stroke="#fff" stroke-width=".9"/><path d="M2.8 4l3.7 2.8L10.2 4" fill="none" stroke="#fff" stroke-width=".9"/></svg>
          info@meridianchiropractic.com
        </li>
        <li class="contact__item">
          <svg class="contact__icon" viewBox="0 0 13 13" aria-hidden="true"><rect width="13" height="13" rx="2" fill="var(--brand-blue)"/><circle cx="6.5" cy="6.5" r="3.6" fill="none" stroke="#fff" stroke-width=".9"/><path d="M2.9 6.5h7.2M6.5 2.9c-1.6 2-1.6 5.2 0 7.2M6.5 2.9c1.6 2 1.6 5.2 0 7.2" fill="none" stroke="#fff" stroke-width=".7"/></svg>
          www.meridianchiropractic.com
        </li>
      </ul>
    </div>
  </section>

</main>
</body>
</html>
```